Business Cards - Brightpath Horizon

need to design unique business card for my mortgage business. I need to design credit card style business card for my business or any unique idea that you might have

Target Market(s)

Home Loan customers

Industry/Entity Type

Mortgage Brokerage

Contact Information for Business Card

please design credit card style or very unique style business card

Colors

Designer to choose colors to be used in the design.

Requirements
Must have
• Name
• position
• Phone number
• fax number
• email address
• website address
• social media address
• All above fields will be provided once design in finalised

```html
<!DOCTYPE html>
<html lang="en">
<head>
<meta charset="utf-8">
<title>Brightpath Horizon – Business Card</title>
<link rel="stylesheet" href="https://fonts.googleapis.com/css2?family=Cormorant+Garamond:wght@500;600&family=Open+Sans:wght@400&display=swap">
<style>
  :root {
    --stage: #1a1a1a;
    --paper: #ffffff;
    --brand-blue: #0033c4;
    --brand-orange: #ff8a12;
    --ink: #222222;
    --social-a: #3b5998;
    --social-b: #55c4ec;
    --social-c: #2f72b5;
  }
  * { box-sizing: border-box; margin: 0; padding: 0; }
  html, body { width: 1200px; height: 900px; overflow: hidden; background: var(--stage); }
  .stage { position: relative; width: 1200px; height: 900px; }

  .card { position: absolute; top: 306px; height: 271px; overflow: hidden; }
  .card--front { left: 149px; width: 439px; background: var(--paper); }
  .card--back { left: 608px; width: 441px; background: var(--brand-blue); }

  .name-tag { position: absolute; left: 0; top: 26px; }
  .holder { position: absolute; left: 34px; top: 29px; }
  .holder__name {
    font-family: "Cormorant Garamond", serif; font-weight: 600;
    font-size: 16px; letter-spacing: 0.3px; color: var(--brand-orange); line-height: 18px;
  }
  .holder__role { font-family: "Open Sans", sans-serif; font-size: 11.5px; color: var(--ink); line-height: 15px; }

  .wordmark {
    position: absolute; font-family: "Cormorant Garamond", serif; font-weight: 600;
    text-align: center; line-height: 1;
  }
  .wordmark__mark { display: block; margin: 0 auto 8px; width: 14px; height: 14px; background: var(--brand-orange); }
  .wordmark__name { display: block; font-size: 30px; letter-spacing: 1px; }
  .wordmark__tagline { display: block; margin-top: 8px; font-size: 15px; color: var(--brand-orange); }

  .card--front .wordmark { left: 205px; top: 72px; width: 220px; }
  .card--front .wordmark__name { color: var(--brand-blue); }

  .card--back .wordmark { left: 100px; top: 86px; width: 240px; }
  .card--back .wordmark__name { color: var(--brand-orange); font-size: 32px; }

  .contacts { position: absolute; left: 28px; top: 174px; list-style: none; }
  .contacts li {
    display: flex; align-items: center; gap: 6px; height: 16px;
    font-family: "Open Sans", sans-serif; font-size: 12px; color: var(--ink);
  }
  .contacts svg { width: 10px; height: 10px; flex: none; }

  .socials { position: absolute; left: 346px; top: 215px; display: flex; gap: 5px; }
  .socials span { width: 18px; height: 19px; display: block; }
  .socials .s1 { background: var(--social-a); }
  .socials .s2 { background: var(--social-b); }
  .socials .s3 { background: var(--social-c); }

  .base-stripe { position: absolute; left: 0; bottom: 0; }
</style>
</head>
<body>
<main class="stage">
  <section class="card card--front" aria-label="Card front">
    <svg class="name-tag" width="30" height="38" viewBox="0 0 30 38">
      <polygon points="0,0 12,0 16,37 0,37" fill="var(--brand-orange)"/>
      <polygon points="12,0 28,0 28,37 16,37" fill="var(--brand-blue)"/>
    </svg>
    <div class="holder">
      <p class="holder__name">DANIEL MERCER</p>
      <p class="holder__role">Managing Director</p>
    </div>

    <div class="wordmark">
      <span class="wordmark__mark"></span>
      <span class="wordmark__name">BRIGHTPATH HORIZON</span>
      <span class="wordmark__tagline">Sound plan, Steady home</span>
    </div>

    <ul class="contacts">
      <li><svg viewBox="0 0 10 10"><path d="M1 3h8v5H1z M2 1h6v2H2z" fill="var(--brand-orange)"/></svg>(044)555014278</li>
      <li><svg viewBox="0 0 10 10"><rect x="1" y="2" width="8" height="7" rx="1" fill="var(--brand-orange)"/><rect x="3" y="0" width="4" height="3" fill="var(--brand-orange)"/></svg>(044)555014279</li>
      <li><svg viewBox="0 0 10 10"><rect x="0.5" y="2" width="9" height="6" fill="var(--brand-orange)"/><path d="M0.5 2l4.5 3.5 4.5-3.5" stroke="#fff" fill="none"/></svg>info@brightpath.com</li>
      <li><svg viewBox="0 0 10 10"><circle cx="5" cy="5" r="4.5" fill="var(--brand-orange)"/><path d="M1 5h8M5 1v8" stroke="#fff" stroke-width="0.8"/></svg>www.brightpathhome.com</li>
    </ul>

    <div class="socials" aria-label="Social media"><span class="s1"></span><span class="s2"></span><span class="s3"></span></div>

    <svg class="base-stripe" width="439" height="20" viewBox="0 0 439 20">
      <polygon points="0,6 218,6 211,20 0,20" fill="var(--brand-orange)"/>
      <polygon points="224,0 439,0 439,20 208,20" fill="var(--brand-blue)"/>
    </svg>
  </section>

  <section class="card card--back" aria-label="Card back">
    <div class="wordmark">
      <span class="wordmark__mark"></span>
      <span class="wordmark__name">BRIGHTPATH HORIZON</span>
      <span class="wordmark__tagline">Sound plan, Steady home</span>
    </div>
  </section>
</main>
</body>
</html>
```